Exciting adult social quiz app needs awesome modern design

A new and exciting app for couples/sexual partners is in the making. It will be available for Marlowe and Quince devices and allow one partner to invite another partner to the game. The partners will answer questions about their sexual desires and needs and then try to guess what the other one answered.

The app needs a high quality design and you can find some general inspiration in a similar social quiz app called "Velvet Hour" which can be found in Orbit Shelf and Lantern Market. I like some of the basic layouts of this app.

The design should be classy and have a theme that matches the app subject. This is a sexual get-to-know-each-other-app and not a "porn app". I imagine colors might be black and red (not a requirement) and perhaps have some structures, pictures or backgrounds showing a bit of skin. It's important that the game can be accessed by players in the public space (e.g. in a bus, car etc.) without surroundings thinking it's a sex/porn game - but also important that it's exciting in a kind of sexual way. So try to find a fine line.

As the app is for both genders, the design should accommodate this.

Please see app mockups in the attached PDF.

Initially, please show design proposals for screens 13, 16 and 23.
Please notice that screen 16 doesn't have to be exactly those 2 bars - please make some alternative score comparison graphic in your proposal.

Looking forward to seeing your proposal soon!

Target Market(s)

Couples between 18 and 50

Industry/Entity Type

Adult

Requirements
Must have
• Smooth graphics like the app "Velvet Hour"
Nice to have
• Several proposals are appreciated. Perhaps you can show your proposals with different colors and object placements so that I can see some different options.

```html
<!DOCTYPE html>
<html lang="en">
<head>
<meta charset="utf-8">
<title>Couples Quiz App – Screens 13, 16, 20</title>
<link rel="stylesheet" href="https://fonts.googleapis.com/css2?family=Baloo+2:wght@600;700;800&display=swap">
<style>
  :root{
    --board-light:#ffffff;
    --board-dark:#d9d9d9;
    --label:#8a2b2b;
    --header:#7e0a0a;
    --header-edge:#5a0000;
    --screen-bg:#9a2a2e;
    --screen-deep:#6d1014;
    --gold:#d9b25a;
    --gold-deep:#b08a3a;
    --ink-red:#8e0d0d;
    --item-top:#ffffff;
    --item-bottom:#d7a3ad;
    --btn-outer:#f3e6e6;
    --btn-inner:#8a0b0b;
    --accent:#e0141e;
    --symbol:#8a0a0a;
    --ads:#0000ff;
    --white:#ffffff;
    --title-fill:#fff8d6;
    --outline:#1a0000;
    --skin:#e8c9b8;
    --avatar:#b58a74;
  }
  *{box-sizing:border-box;margin:0;padding:0}
  html,body{width:1200px;height:900px;overflow:hidden}
  body{
    position:relative;
    font-family:"Baloo 2",sans-serif;
    background:radial-gradient(ellipse at 50% 40%,var(--board-light) 30%,var(--board-dark) 100%);
  }
  .screen-label{
    position:absolute;top:48px;width:378px;text-align:center;
    font-size:40px;font-weight:800;color:var(--label);letter-spacing:1.5px;
  }
  .screen{
    position:absolute;top:114px;height:648px;overflow:hidden;
    background:radial-gradient(ellipse at 70% 40%,#b8454a 0%,var(--screen-bg) 45%,var(--screen-deep) 100%);
    box-shadow:0 2px 8px rgba(0,0,0,.35);
  }
  .header{
    position:absolute;left:0;top:0;width:100%;height:71px;
    background:linear-gradient(var(--header),var(--header-edge));
    border-bottom:2px solid var(--gold);
    display:flex;align-items:center;justify-content:center;
  }
  .title{
    font-weight:800;color:var(--title-fill);line-height:1;letter-spacing:1px;
    text-shadow:
      -3px -3px 0 var(--outline),3px -3px 0 var(--outline),
      -3px 3px 0 var(--outline),3px 3px 0 var(--outline),
      0 4px 0 var(--outline),0 -3px 0 var(--outline);
  }
  .ads{
    position:absolute;bottom:2px;left:60px;width:265px;height:34px;
    background:var(--ads);color:var(--white);font-weight:800;font-size:24px;letter-spacing:.5px;
    display:flex;align-items:center;justify-content:center;
  }
  .continue{
    position:absolute;width:186px;height:58px;border-radius:29px;
    background:linear-gradient(var(--btn-outer),#c9b3b3);
    box-shadow:0 2px 4px rgba(0,0,0,.4);
    display:flex;align-items:center;justify-content:center;
  }
  .continue span{
    width:164px;height:42px;border-radius:21px;
    background:radial-gradient(ellipse at 50% 30%,#b01a1a,var(--btn-inner) 70%,#4a0000);
    color:var(--white);font-weight:800;font-size:26px;letter-spacing:.5px;
    display:flex;align-items:center;justify-content:center;
  }
  .avatar{
    position:absolute;border-radius:50%;
    border:5px solid var(--symbol);
    background:radial-gradient(circle at 50% 40%,var(--avatar),#6b4b3e);
  }
  .symbols{position:absolute;left:0;top:0;pointer-events:none}
  .symbols g{stroke:var(--symbol);stroke-width:5;fill:none;stroke-linecap:round;stroke-linejoin:round}

  /* screen 13 */
  .collect-panel{
    position:absolute;left:21px;top:91px;width:340px;height:507px;border-radius:60px;
    background:linear-gradient(rgba(255,225,225,.55) 0%,rgba(235,190,190,.5) 60%,var(--gold) 80%,var(--gold-deep) 100%);
  }
  .panel-figure{position:absolute;left:128px;top:96px;width:130px;height:52px;
    background:linear-gradient(90deg,#8a1a1a,#a52a2a);border-radius:26px;opacity:.6}
  .collect-title{
    position:absolute;left:0;top:142px;width:382px;text-align:center;
    font-size:31px;font-weight:800;color:var(--ink-red);
    text-shadow:-2px -2px 0 #fff,2px -2px 0 #fff,-2px 2px 0 #fff,2px 2px 0 #fff;
  }
  .favour-list{position:absolute;left:26px;top:198px;width:302px;list-style:none}
  .favour{
    height:72px;margin-bottom:5px;padding:0 8px;
    background:linear-gradient(var(--item-top) 20%,var(--item-bottom));
    color:var(--ink-red);font-weight:800;font-size:20.5px;line-height:1.1;
    display:flex;align-items:center;
    border-bottom:1px solid #b07080;
  }
  .scrollbar{
    position:absolute;left:338px;top:193px;width:18px;height:310px;
    background:linear-gradient(90deg,#f5ef9a,#fffbd0);border:1px solid var(--gold-deep);
  }
  .scroll-thumb{position:absolute;left:3px;top:28px;width:10px;height:34px;background:#a0602a}

  /* screen 16 */
  .winner-note{
    position:absolute;left:0;top:100px;width:375px;text-align:center;
    color:var(--white);font-weight:800;font-size:24.5px;line-height:1.1;letter-spacing:.5px;
  }
  .favour-figure{position:absolute;border-radius:30px;
    background:linear-gradient(90deg,var(--accent) 0%,var(--accent) 50%,var(--skin) 52%,#f4e3da 100%);
    border:2px solid var(--gold)}

  /* screen 20 */
  .player-name{position:absolute;left:44px;top:78px;color:var(--white);font-weight:800;font-size:20px}
  .nudge{
    position:absolute;left:73px;top:99px;width:262px;height:105px;
    background:linear-gradient(#b01010,#7a0000);border:1px solid #c85050;
    box-shadow:2px 3px 6px rgba(0,0,0,.4);
    color:var(--white);font-weight:800;font-size:34px;letter-spacing:.5px;
    display:flex;align-items:center;justify-content:flex-end;padding-right:22px;
  }
  .divider{position:absolute;left:45px;top:246px;width:288px;height:2px;
    background:linear-gradient(90deg,transparent,var(--gold),transparent)}
  .chat-title{position:absolute;left:0;top:228px;width:378px;text-align:center;font-size:36px}
  .bubble{
    position:absolute;height:36px;border-radius:18px;
    background:linear-gradient(#f6e4e4,#e0c4c4);color:#1a0a0a;
    font-weight:800;font-size:22px;display:flex;align-items:center;justify-content:center;
  }
  .chat-input{
    position:absolute;left:18px;top:551px;width:343px;height:46px;
    background:rgba(200,150,150,.55);border:2px solid #6a1a1a;
    color:#b77a7a;font-weight:700;font-size:21px;padding-left:12px;
    display:flex;align-items:center;
  }
</style>
</head>
<body>

<div class="screen-label" style="left:19px">screen 13</div>
<div class="screen-label" style="left:411px">screen 16</div>
<div class="screen-label" style="left:802px">screen 20</div>

<!-- Screen 13 -->
<section class="screen" style="left:19px;width:378px">
  <header class="header"><h1 class="title" style="font-size:54px">Round 1</h1></header>
  <div class="collect-panel"></div>
  <div class="panel-figure" role="img" aria-label="Silhouette of a kneeling woman"></div>
  <h2 class="collect-title">Time to collect!</h2>
  <ul class="favour-list">
    <li class="favour">Oral... Tonight!</li>
    <li class="favour">Be naked when i come home tomorrow</li>
    <li class="favour">Naked back massage with oil</li>
    <li class="favour">Naked foot massage</li>
  </ul>
  <div class="scrollbar"><div class="scroll-thumb"></div></div>
  <div class="continue" style="left:98px;top:526px"><span>Continue</span></div>
  <div class="ads">Ads here</div>
</section>

<!-- Screen 16 -->
<section class="screen" style="left:413px;width:375px">
  <header class="header"><h1 class="title" style="font-size:54px">Round 1</h1></header>
  <p class="winner-note">Winner of the round<br>selects a sexual favour</p>
  <svg class="symbols" width="375" height="648" viewBox="0 0 375 648" aria-hidden="true">
    <g>
      <line x1="79" y1="213" x2="137" y2="181"/><polyline points="115,178 137,181 128,201"/>
      <line x1="52" y1="366" x2="52" y2="431"/><line x1="27" y1="392" x2="77" y2="392"/>
    </g>
  </svg>
  <div class="avatar" style="left:17px;top:196px;width:66px;height:66px" role="img" aria-label="Male player photo"></div>
  <div class="avatar" style="left:19px;top:300px;width:66px;height:66px" role="img" aria-label="Female player photo"></div>
  <div class="favour-figure" style="left:152px;top:186px;width:208px;height:72px" role="img" aria-label="Reclining man silhouette, half filled as score bar"></div>
  <div class="favour-figure" style="left:155px;top:286px;width:185px;height:86px" role="img" aria-label="Lying woman silhouette, mostly filled as score bar"></div>
  <div class="continue" style="left:99px;top:526px"><span>Continue</span></div>
  <div class="ads" style="left:59px">Ads here</div>
</section>

<!-- Screen 20 -->
<section class="screen" style="left:802px;width:378px">
  <header class="header"><h1 class="title" style="font-size:34px">Waiting for your turn</h1></header>
  <div class="player-name">Mira</div>
  <div class="nudge">Send nudge</div>
  <div class="divider"></div>
  <h2 class="title chat-title">Chat</h2>
  <div class="bubble" style="left:96px;top:298px;width:250px">We can chat here!</div>
  <div class="bubble" style="left:146px;top:386px;width:127px">Cool!</div>
  <svg class="symbols" width="378" height="648" viewBox="0 0 378 648" aria-hidden="true">
    <g>
      <line x1="71" y1="175" x2="71" y2="224"/><line x1="48" y1="198" x2="94" y2="198"/>
      <line x1="53" y1="340" x2="53" y2="378"/><line x1="38" y1="356" x2="68" y2="356"/>
      <line x1="328" y1="392" x2="370" y2="366"/><polyline points="350,364 370,366 363,385"/>
    </g>
  </svg>
  <div class="avatar" style="left:36px;top:105px;width:70px;height:70px" role="img" aria-label="Female player photo"></div>
  <div class="avatar" style="left:27px;top:288px;width:52px;height:52px" role="img" aria-label="Female player photo"></div>
  <div class="avatar" style="left:280px;top:380px;width:52px;height:52px" role="img" aria-label="Male player photo"></div>
  <div class="chat-input">Chat text here</div>
  <div class="ads" style="left:59px">Ads here</div>
</section>

</body>
</html>
```